Hollow Thicket, a 3d voxel survival video game needs a card for gaming conventions

I am the lead developer for Hollow Thicket http://www.HollowThicket.example and need a business card to hand out at an indie gaming convention
The card would need to include the game name, website url, my name, position (Lead Developer), e-mail and phone number
The game is a 3d, voxel (with smooth terrain) based survival game with guns and wildlife. The main icon of the game would likely be a grizzly bear but I am willing to accept other designs too.
Attached is a media kit for the game with some images you can use but don't have to its just what little art I can provide. Anything on the website or from the video game can also be used. unrelated art can also be used.
Target Market(s)
Indie Developers/publishers at conferences
Industry/Entity Type
Games
Contact Information for Business Card
Name: Corin Waldrick
Position: Lead Developer
E-mail: Pale_Kettle@mailbox.example
Phone number: 555-372-1186

```html
<!DOCTYPE html>
<html lang="en">
<head>
<meta charset="utf-8">
<title>Hollow Thicket — Business Card</title>
<link rel="stylesheet" href="https://fonts.googleapis.com/css2?family=Source+Sans+3:wght@400;600;800&display=swap">
<style>
  :root {
    --backdrop: #ece8e2;
    --card-red: #8e1a11;
    --card-red-deep: #a3160c;
    --card-tan: #b08a50;
    --card-tan-light: #b59a62;
    --title-tan: #b99f68;
    --title-red: #9b1d12;
    --paper: #ffffff;
    --fur-dark: #4a2412;
    --fur-mid: #8a4a26;
    --text-light: #ffffff;
  }
  * { box-sizing: border-box; margin: 0; padding: 0; }
  html, body {
    width: 1200px;
    height: 900px;
    overflow: hidden;
    background: var(--backdrop);
    font-family: "Source Sans 3", "Myriad Pro", sans-serif;
  }
  .canvas {
    position: relative;
    width: 1200px;
    height: 900px;
  }
  .card {
    position: absolute;
    left: 250px;
    width: 700px;
    height: 400px;
    overflow: hidden;
    box-shadow: 0 10px 28px rgba(0,0,0,0.22);
  }

  /* Front */
  .card--front {
    top: 36px;
    background: linear-gradient(200deg, var(--card-tan-light) 0%, #a8724a 40%, var(--card-red-deep) 100%);
  }
  .front__artwork {
    position: absolute;
    left: 40px;
    top: 40px;
    width: 270px;
    height: 200px;
    border-radius: 45% 45% 30% 30%;
    background: radial-gradient(ellipse at 55% 40%, var(--fur-mid) 0%, var(--fur-dark) 60%, rgba(74,36,18,0) 80%);
  }
  .front__title {
    position: absolute;
    left: 160px;
    top: 250px;
    font-weight: 800;
    font-size: 52px;
    line-height: 1;
    letter-spacing: 3px;
    text-transform: uppercase;
    white-space: nowrap;
    color: var(--title-tan);
  }

  /* Back */
  .card--back {
    top: 464px;
    background: var(--paper);
  }
  .back__brand {
    height: 140px;
    display: flex;
    align-items: center;
    justify-content: center;
  }
  .back__title {
    font-weight: 800;
    font-size: 46px;
    line-height: 1;
    letter-spacing: 3px;
    text-transform: uppercase;
    color: var(--title-red);
  }
  .back__identity {
    height: 100px;
    background: var(--card-red);
    color: var(--text-light);
    text-align: center;
    padding-top: 22px;
  }
  .identity__name {
    font-weight: 600;
    font-size: 22px;
    letter-spacing: 0.5px;
    text-transform: uppercase;
  }
  .identity__role {
    font-size: 16px;
    margin-top: 2px;
  }
  .back__divider {
    height: 8px;
    background: var(--paper);
  }
  .back__contact {
    height: 152px;
    background: var(--card-tan);
    color: var(--text-light);
    text-align: center;
    padding-top: 26px;
    font-size: 18px;
    line-height: 1.4;
  }
</style>
</head>
<body>
<main class="canvas">
  <section class="card card--front" aria-label="Card front">
    <div class="front__artwork" role="img" aria-label="Photograph of a roaring grizzly bear"></div>
    <h1 class="front__title">Hollow Thicket</h1>
  </section>

  <section class="card card--back" aria-label="Card back">
    <div class="back__brand">
      <h2 class="back__title">Hollow Thicket</h2>
    </div>
    <div class="back__identity">
      <p class="identity__name">Corin Waldrick</p>
      <p class="identity__role">Lead Developer</p>
    </div>
    <div class="back__divider"></div>
    <div class="back__contact">
      <p class="contact__phone">555-372-1186</p>
      <p class="contact__email">Pale_Kettle@mailbox.example</p>
      <p class="contact__web">www.HollowThicket.example</p>
    </div>
  </section>
</main>
</body>
</html>
```